Luxury Toilet Rental Business. Tallowby Hire.

Tallowby Hire (the logo is in the uploaded files)
We RENT and SELL Luxury Trailer toilets.
- Show location, number, pricing, pictures.
- We have two stall trailers for rent AND 3 stall trailers
- We sell them too
- We want our phone number shown
- We are a local company
- Slogan: Brighten your gathering with Tallowby Hire. The Velvet Privy
- We want a pricing portion
- We want the sizes shown
- We want the different rates/ prices shown
- We do 1 day rentals
- We do 1 week rentals
- We want the service area. We serve Los Angeles County, Orange County, Riverside County, San Bernardino County, and Palm Desert.
- Our location is in Santa Ana California

Target Market(s)

Event planners, wedding planners, venue planners, concerts, events, gatherings.

Industry/Entity Type

Luxury Toilet Rentals

Number of Pages Required

1 page

Font styles to use
Serif
Sans Serif

Colors
EE7325
F08F49
F5BC92
FAE3D3
FDF4ED

Requirements
Must have
• Location, pricing, pictures, available areas. Our slogan.
Nice to have
• I like the idea of having tabs that show price, a tab that shows our contact information, pictures, event ideas, and where we service (the areas we'll go to)

```html
<!DOCTYPE html>
<html lang="en">
<head>
<meta charset="UTF-8">
<title>Tallowby Hire — Luxury Restroom Trailers</title>
<link href="https://fonts.googleapis.com/css2?family=Work+Sans:wght@300;400;500;600;700&display=swap" rel="stylesheet">
<style>
:root{
  --orange:#EE7325;
  --orange-2:#F08F49;
  --peach:#F5BC92;
  --cream:#FAE3D3;
  --shell:#FDF4ED;
  --white:#ffffff;
  --ink:#3a3a3a;
  --grey:#666;
}
*{box-sizing:border-box;margin:0;padding:0}
html,body{width:1200px;height:3575px;overflow:hidden}
body{font-family:"Work Sans",Arial,sans-serif;color:var(--ink);background:var(--white)}
.wrap{width:958px;margin:0 auto;position:relative}
a{text-decoration:none;color:inherit}
.brand{font-weight:700;font-size:22px;color:var(--white);display:flex;align-items:center;gap:8px;letter-spacing:.5px}
.brand i{width:12px;height:12px;background:var(--white);display:block}

/* nav */
.nav{height:100px;background:var(--orange);display:flex;align-items:center}
.nav .wrap{display:flex;align-items:center;justify-content:space-between}
.menu{display:flex;align-items:center;gap:32px;color:var(--white);font-size:16px}
.menu .active{font-weight:700}
.menu .cta{background:var(--white);color:var(--orange);font-weight:600;padding:11px 18px;border-radius:3px}

/* hero */
.hero{height:666px;position:relative;display:flex;flex-direction:column;align-items:center;justify-content:center;text-align:center}
.hero .photo{position:absolute;inset:0;background:linear-gradient(160deg,#4a4a4a,#2c2c2c 50%,#3d3a36)}
.hero h1{position:relative;font-weight:300;font-size:55px;line-height:62px;color:var(--white);width:860px}
.hero h1 span{color:var(--orange);font-weight:400}
.hero .btns{position:relative;display:flex;gap:20px;margin-top:46px}
.btn-fill{width:225px;height:42px;background:var(--orange);color:var(--white);font-weight:700;font-size:16px;display:flex;align-items:center;justify-content:center}
.btn-line{width:225px;height:42px;border:1px solid var(--white);color:var(--white);font-size:16px;display:flex;align-items:center;justify-content:center}

/* own */
.own{height:709px;background:var(--orange);padding-top:48px;color:var(--white);text-align:center}
.own h2{font-weight:400;font-size:29px;margin-bottom:22px}
.own p.lead{font-size:16px;line-height:23.5px;margin-bottom:22px}
.products{display:flex;gap:20px}
.pcard{width:306px;height:381px;background:var(--white);border-radius:4px;overflow:hidden;text-align:left}
.pcard .img{height:208px;background:linear-gradient(135deg,#e9e6e2,#bdb9b4)}
.pcard .body{padding:22px 20px}
.pcard h3{color:var(--orange);font-size:16px;font-weight:700;margin-bottom:14px}
.pcard p{font-size:11px;line-height:17px;color:var(--grey);text-align:justify;margin-bottom:8px}
.pcard .go{height:42px;background:var(--orange);color:var(--white);font-weight:700;font-size:16px;display:flex;align-items:center;justify-content:center;border-radius:3px}
.more-line{margin-top:20px;height:43px;border:1px solid var(--white);display:flex;align-items:center;justify-content:center;font-size:16px;border-radius:2px}

/* about */
.about{height:333px;position:relative;text-align:center;color:var(--white);padding-top:34px}
.about .photo{position:absolute;inset:0;background:linear-gradient(90deg,var(--orange-2),#e9853f 50%,var(--orange-2))}
.about .wrap{position:relative}
.about h2{font-size:29px;font-weight:600;margin-bottom:18px}
.about p{font-size:16px;line-height:23.5px;margin-bottom:22px}
.about .btn-line{margin:0 auto}

/* trailers */
.trailers{height:749px;padding-top:50px;text-align:center}
.trailers h2{color:var(--orange);font-size:29px;font-weight:500;margin-bottom:23px}
.tgrid{display:flex;gap:19px}
.tcard{width:470px;height:527px;border-radius:4px;box-shadow:0 1px 6px rgba(0,0,0,.12);overflow:hidden;text-align:left}
.tcard .img{height:310px;background:linear-gradient(180deg,#cdd3d8,#9aa0a5 55%,#8d8a86)}
.tcard .body{padding:26px 20px}
.tcard .top{display:flex;justify-content:space-between;align-items:flex-start}
.tcard h3{color:var(--orange);font-size:29px;font-weight:600;margin-top:4px}
.price{text-align:right;font-size:12px;color:var(--orange);line-height:23px}
.price b{font-weight:700}
.tcard p{font-size:16px;line-height:23.5px;color:var(--grey);margin:28px 0 20px}
.tcard .acts{display:flex;gap:12px}
.q{width:143px;height:43px;border:1px solid var(--orange);color:var(--orange);font-weight:600;font-size:16px;display:flex;align-items:center;justify-content:center;border-radius:2px}
.r{flex:1;height:43px;background:var(--orange);color:var(--white);font-weight:700;font-size:16px;display:flex;align-items:center;justify-content:center;border-radius:2px}
.trailers .more-line{border-color:var(--orange);color:var(--orange)}

/* coverage */
.coverage{height:433px;background:var(--orange);color:var(--white);text-align:center;padding-top:40px}
.coverage h2{font-size:29px;font-weight:400;margin-bottom:26px}
.areas{display:flex;flex-wrap:wrap;justify-content:center;gap:20px}
.area{width:306px;height:103px;border:1px solid var(--white);text-align:left;padding:10px 10px}
.area h3{font-size:15px;font-weight:700;display:flex;align-items:center;gap:6px;margin-bottom:9px}
.area p{font-size:11px;line-height:17px}
.coverage .more-line{margin-top:20px}

/* contact */
.contact{height:250px;position:relative;text-align:center;padding-top:44px}
.contact .photo{position:absolute;inset:0;background:linear-gradient(100deg,#f7f7f7,#ececec 60%,#f4f4f4)}
.contact .wrap{position:relative}
.contact h2{color:var(--orange);font-size:29px;font-weight:600;margin-bottom:18px}
.contact p{color:var(--orange);font-size:16px;line-height:23.5px;width:600px;margin:0 auto 22px}
.contact .btns{display:flex;gap:20px;justify-content:center}
.contact .btn-line{border-color:var(--orange);color:var(--orange);gap:8px}
.contact .btn-fill{font-weight:500;gap:8px}

/* footer */
.footer{height:335px;background:var(--orange);color:var(--white);padding-top:42px}
.fcols{display:flex;height:210px}
.fbrand{width:326px}
.fbrand .loc{display:flex;gap:8px;align-items:center;font-size:16px;margin:26px 0 30px}
.fbrand h4{font-size:16px;font-weight:700;margin-bottom:20px}
.fbrand .line{font-size:16px;margin-bottom:8px}
.fcol{width:245px}
.fcol h4{font-size:16px;font-weight:700;margin:0 0 16px}
.fcol a{display:block;font-size:16px;margin-bottom:13px}
.fbottom{border-top:1px solid var(--peach);padding-top:14px;display:flex;justify-content:space-between;align-items:center;font-size:11px}
.social{display:flex;gap:14px}
.social span{width:20px;height:20px;border-radius:50%;background:var(--white);display:block;opacity:.85}
</style>
</head>
<body>

<header class="nav">
  <div class="wrap">
    <a class="brand" href="#"><i></i>TALLOWBY</a>
    <nav class="menu">
      <a class="active" href="#">Home</a>
      <a href="#">Restroom Trailers ▾</a>
      <a href="#">Services ▾</a>
      <a href="#">Gallery</a>
      <a href="#">About Us</a>
      <a class="cta" href="#">Contact Us ↗</a>
    </nav>
  </div>
</header>

<section class="hero">
  <div class="photo" role="img" aria-label="Interior of a luxury restroom trailer with vanity sink and toilet"></div>
  <h1>Brighten your gathering with <span>Tallowby</span> Hire. The Velvet Privy.</h1>
  <div class="btns">
    <a class="btn-fill" href="#">BOOK NOW!</a>
    <a class="btn-line" href="#">Our Services</a>
  </div>
</section>

<section class="own">
  <div class="wrap">
    <h2>Own Your Velvet Privy</h2>
    <p class="lead">In addition to our rental services, Tallowby Hire offers the opportunity for you to own your own luxury trailer toilet. Whether you're a recurring event organizer or simply prefer the convenience of having one on hand, our sales options provide you with the same high-quality products that we rent out. Contact us today to learn more about our purchasing process and available models</p>
    <div class="products">
      <article class="pcard">
        <div class="img" role="img" aria-label="Trailer interior with white vanity sink"></div>
        <div class="body"><h3>Fernhollow Co</h3><p>In et eu morbi dui dolor nibh suspendisse orci. Integer sodales felis morbi purus tincidunt purus.</p><a class="go" href="#">View Details ↗</a></div>
      </article>
      <article class="pcard">
        <div class="img" role="img" aria-label="Trailer interior with sink and toilet"></div>
        <div class="body"><h3>Ashbury Ltd</h3><p>In et eu morbi dui dolor nibh suspendisse orci. Integer sodales felis morbi purus tincidunt purus.</p><a class="go" href="#">View Details ↗</a></div>
      </article>
      <article class="pcard">
        <div class="img" role="img" aria-label="Compact trailer restroom with vanity and toilet"></div>
        <div class="body"><h3>Quillmere Group</h3><p>In et eu morbi dui dolor nibh suspendisse orci. Integer sodales felis morbi purus tincidunt purus.</p><a class="go" href="#">View Details ↗</a></div>
      </article>
    </div>
    <a class="more-line" href="#">More Product ›</a>
  </div>
</section>

<section class="about">
  <div class="photo" role="img" aria-label="Restroom trailers parked in a yard, orange tinted"></div>
  <div class="wrap">
    <h2>About Us</h2>
    <p>Tallowby Hire is your premier destination for luxury trailer toilets. With a commitment to exceptional service and quality, we offer a range of rental and sales options tailored to elevate your event experience. Based in Santa Ana, California, we proudly serve Los Angeles County, Orange County, Riverside County, San Bernardino County, and Palm Desert. Discover the luxury of Tallowby Hire and make your event unforgettable</p>
    <a class="btn-line" href="#">More Details</a>
  </div>
</section>

<section class="trailers">
  <div class="wrap">
    <h2>Restroom Trailers</h2>
    <div class="tgrid">
      <article class="tcard">
        <div class="img" role="img" aria-label="Grey two stall restroom trailer with steps"></div>
        <div class="body">
          <div class="top"><h3>2 Stall Trailers - 001</h3><div class="price"><b>$50</b>/day<br><b>$250</b>/week</div></div>
          <p>In et eu morbi dui dolor nibh suspendisse orci. Integer sodales felis morbi purus tincidunt purus.</p>
          <div class="acts"><a class="q" href="#">Quick Quote</a><a class="r" href="#">Rent It ↗</a></div>
        </div>
      </article>
      <article class="tcard">
        <div class="img" role="img" aria-label="Grey three stall restroom trailer with blue steps"></div>
        <div class="body">
          <div class="top"><h3>3 Stall Trailers - 002</h3><div class="price"><b>$50</b>/day<br><b>$250</b>/week</div></div>
          <p>Nam dictum mauris purus est. Porttitor ipsum tempor etiam blandit ut nibh.</p>
          <div class="acts"><a class="q" href="#">Quick Quote</a><a class="r" href="#">Rent It ↗</a></div>
        </div>
      </article>
    </div>
    <a class="more-line" href="#">More Deals ›</a>
  </div>
</section>

<section class="coverage">
  <div class="wrap">
    <h2>Discover Our Extensive Service Coverage</h2>
    <div class="areas">
      <div class="area"><h3><svg width="14" height="16" viewBox="0 0 14 16" fill="none" stroke="#fff" stroke-width="1.4"><path d="M7 15s5-5 5-9A5 5 0 0 0 2 6c0 4 5 9 5 9z"/><circle cx="7" cy="6" r="1.8"/></svg>Los Angeles County</h3><p>Serving all of Los Angeles County, including cities such as Los Angeles, Long Beach, Santa Monica, and Beverly Hills.</p></div>
      <div class="area"><h3><svg width="14" height="16" viewBox="0 0 14 16" fill="none" stroke="#fff" stroke-width="1.4"><path d="M7 15s5-5 5-9A5 5 0 0 0 2 6c0 4 5 9 5 9z"/><circle cx="7" cy="6" r="1.8"/></svg>Orange County</h3><p>We cover areas in Orange County, including cities such as Anaheim, Irvine, Newport Beach, and Laguna Beach.</p></div>
      <div class="area"><h3><svg width="14" height="16" viewBox="0 0 14 16" fill="none" stroke="#fff" stroke-width="1.4"><path d="M7 15s5-5 5-9A5 5 0 0 0 2 6c0 4 5 9 5 9z"/><circle cx="7" cy="6" r="1.8"/></svg>Riverside County</h3><p>Our service extends to Riverside County, including cities such as Riverside, Palm Springs, Temecula, and Indio.</p></div>
      <div class="area"><h3><svg width="14" height="16" viewBox="0 0 14 16" fill="none" stroke="#fff" stroke-width="1.4"><path d="M7 15s5-5 5-9A5 5 0 0 0 2 6c0 4 5 9 5 9z"/><circle cx="7" cy="6" r="1.8"/></svg>San Bernardino County</h3><p>We also cater to locations in San Bernardino County, including cities such as San Bernardino, Ontario, Fontana, and Rancho Cucamonga.</p></div>
      <div class="area"><h3><svg width="14" height="16" viewBox="0 0 14 16" fill="none" stroke="#fff" stroke-width="1.4"><path d="M7 15s5-5 5-9A5 5 0 0 0 2 6c0 4 5 9 5 9z"/><circle cx="7" cy="6" r="1.8"/></svg>Palm Desert</h3><p>Our services are available in Palm Desert and surrounding areas.</p></div>
    </div>
    <a class="more-line" href="#">Find Locations ›</a>
  </div>
</section>

<section class="contact">
  <div class="photo" role="img" aria-label="Faded restroom trailer interior"></div>
  <div class="wrap">
    <h2>Contact Us</h2>
    <p>Have a question or need assistance? Don't hesitate to reach out to our friendly team. We're ready to assist you!</p>
    <div class="btns">
      <a class="btn-fill" href="#"><svg width="14" height="14" viewBox="0 0 24 24" fill="#fff"><path d="M6.6 10.8a15 15 0 0 0 6.6 6.6l2.2-2.2a1 1 0 0 1 1-.25 11 11 0 0 0 3.6.6 1 1 0 0 1 1 1V20a1 1 0 0 1-1 1A17 17 0 0 1 3 4a1 1 0 0 1 1-1h3.5a1 1 0 0 1 1 1 11 11 0 0 0 .6 3.6 1 1 0 0 1-.25 1z"/></svg>Contact Support</a>
      <a class="btn-line" href="#"><svg width="16" height="12" viewBox="0 0 16 12" fill="#EE7325"><path d="M0 0h16v12H0z"/><path d="M0 0l8 6 8-6" stroke="#fff" stroke-width="1.3" fill="none"/></svg>Email</a>
    </div>
  </div>
</section>

<footer class="footer">
  <div class="wrap">
    <div class="fcols">
      <div class="fbrand">
        <div class="brand"><i></i>TALLOWBY</div>
        <div class="loc"><svg width="14" height="16" viewBox="0 0 14 16" fill="none" stroke="#fff" stroke-width="1.4"><path d="M7 15s5-5 5-9A5 5 0 0 0 2 6c0 4 5 9 5 9z"/><circle cx="7" cy="6" r="1.8"/></svg>Santa Ana California</div>
        <h4>Contact Us</h4>
        <div class="line"><b>Phone:</b> (000) 000-4417</div>
        <div class="line"><b>Mail:</b> info@tallowbyhire.com</div>
      </div>
      <div class="fcol"><h4>Service</h4><a href="#">Our Team</a><a href="#">Service Area</a><a href="#">Restroom Trailers</a></div>
      <div class="fcol"><h4>Product</h4><a href="#">Sell/Trade</a><a href="#">Rental Info</a><a href="#">Delivery Information</a></div>
      <div class="fcol"><h4>Support</h4><a href="#">About Us</a><a href="#">Contact Support</a><a href="#">Responsible</a><a href="#">Careers</a></div>
    </div>
    <div class="fbottom">
      <span>Copyright © 2024 Tallowby Hire. All rights reserved</span>
      <div class="social"><span></span><span></span><span></span></div>
    </div>
  </div>
</footer>

</body>
</html>
```